Bright Harbor Counseling Letterhead for hip modern business

I would like some ombre use of the colors in the logo hip letterhead that incorporates logo colors and feel, needs to connect with young professionals and college students. i need to be able to write letters to schools to excuse absences as well. i like color blocks on one side preferably using colors from the attached logo design.

Target Market(s)

high income young people, young adults and college students

Industry/Entity Type

mental health

Font styles to use
Serif
Sans Serif

Colors
0054AA
0677BA
7BADD7
CADEEF
E8F1F8
0094D4
00A9DD
6FCCEA
C7EBF8
E9F6FB
00AB8E
00BBA5
67D7C9
C6EFE9
E9F9F6
59FF00
82FF00
B8FF75
E3FFCB
F4FFEA
A7469A
B969AE
D3A5CF
EDDBEB
F8F0F9
6B429C
8869AF
B7A5CE
E3DAEB
F3F0F8

Requirements
Must have
• a modern hip feel, somewhat color

```html
<!DOCTYPE html>
<html lang="en">
<head>
<meta charset="utf-8">
<title>Bright Harbor Counseling Letterhead</title>
<link href="https://fonts.googleapis.com/css2?family=Open+Sans:wght@300;400;700&display=swap" rel="stylesheet">
<style>
  :root {
    --backdrop: #e6ecf3;
    --paper: #ffffff;
    --plum: #a7469a;
    --orchid: #b969ae;
    --violet: #6b429c;
    --sky: #6fccea;
    --teal: #00bba5;
    --ink: #4a4a4a;
    --ink-soft: #6d6d6d;
    --rule: #9a9a9a;
  }
  html, body {
    margin: 0;
    width: 1200px;
    height: 784px;
    overflow: hidden;
    background: var(--backdrop);
    font-family: "Open Sans", Arial, sans-serif;
  }
  .letterhead {
    position: absolute;
    left: 360px;
    top: 22px;
    width: 480px;
    height: 740px;
    background: var(--paper);
    box-shadow: 0 6px 18px rgba(40, 70, 110, 0.18);
    overflow: hidden;
  }
  .side-blocks {
    position: absolute;
    left: 0;
    top: 0;
    width: 26px;
    height: 740px;
    display: flex;
    flex-direction: column;
  }
  .side-blocks .block { flex: 1; }
  .side-blocks .block-violet { background: linear-gradient(180deg, var(--violet), #8869af); }
  .side-blocks .block-plum { background: linear-gradient(180deg, var(--orchid), var(--plum)); flex: 2; }
  .side-blocks .block-sky { background: linear-gradient(180deg, var(--sky), #00a9dd); }
  .side-blocks .block-teal { background: linear-gradient(180deg, #67d7c9, var(--teal)); }
  .side-accent {
    position: absolute;
    left: 32px;
    top: 0;
    width: 3px;
    height: 740px;
    background: linear-gradient(180deg, var(--violet), var(--plum) 50%, var(--teal));
    opacity: 0.5;
  }
  .brand {
    position: absolute;
    right: 40px;
    top: 42px;
    display: flex;
    align-items: center;
    gap: 10px;
    color: var(--ink);
    font-weight: 300;
  }
  .brand-name { line-height: 1; text-align: right; }
  .brand-name .primary {
    display: block;
    font-size: 25px;
    letter-spacing: 0.2px;
  }
  .brand-name .secondary {
    display: block;
    font-size: 12px;
    letter-spacing: 3.2px;
    margin-top: 4px;
  }
  .brand-dot {
    width: 22px;
    height: 22px;
    border-radius: 50%;
    background: var(--violet);
  }
  .contact-block {
    position: absolute;
    left: 40px;
    right: 14px;
    bottom: 30px;
    display: flex;
    flex-direction: column;
    align-items: center;
    gap: 6px;
  }
  .address-row {
    display: flex;
    align-items: center;
    gap: 8px;
    font-size: 8.5px;
    font-weight: 700;
    color: var(--plum);
    white-space: nowrap;
  }
  .address-row .rule {
    width: 44px;
    height: 1px;
    background: var(--rule);
  }
  .icon-row { display: flex; gap: 9px; }
  .icon-row svg { width: 12px; height: 12px; display: block; }
  .details-row {
    font-size: 8px;
    color: var(--ink-soft);
    white-space: nowrap;
  }
  .details-row .sep { color: var(--plum); margin: 0 5px; }
</style>
</head>
<body>
  <main class="letterhead">
    <div class="side-blocks" aria-hidden="true">
      <span class="block block-violet"></span>
      <span class="block block-plum"></span>
      <span class="block block-sky"></span>
      <span class="block block-teal"></span>
    </div>
    <span class="side-accent" aria-hidden="true"></span>

    <header class="brand">
      <div class="brand-name">
        <span class="primary">Bright Harbor</span>
        <span class="secondary">Counseling</span>
      </div>
      <span class="brand-dot"></span>
    </header>

    <footer class="contact-block">
      <div class="address-row">
        <span class="rule"></span>
        <span>0000 Sample Avenue, Suite 210, Portland, OR 97201</span>
        <span class="rule"></span>
      </div>
      <div class="icon-row">
        <svg viewBox="0 0 12 12" aria-label="Address"><circle cx="6" cy="6" r="6" fill="var(--plum)"/><path d="M6 2.6a2.2 2.2 0 0 0-2.2 2.2C3.8 6.6 6 9.4 6 9.4s2.2-2.8 2.2-4.6A2.2 2.2 0 0 0 6 2.6z" fill="#fff"/><circle cx="6" cy="4.8" r="0.8" fill="var(--plum)"/></svg>
        <svg viewBox="0 0 12 12" aria-label="Phone"><circle cx="6" cy="6" r="6" fill="var(--plum)"/><path d="M4.2 3c.4 0 .9 1.2.7 1.5l-.4.5c.4.9 1.1 1.6 2 2l.5-.4c.3-.2 1.5.3 1.5.7 0 .7-.6 1.2-1.2 1.1C5.2 8.1 3.9 6.8 3.6 4.7 3.5 3.8 3.8 3 4.2 3z" fill="#fff"/></svg>
        <svg viewBox="0 0 12 12" aria-label="Fax"><circle cx="6" cy="6" r="6" fill="var(--plum)"/><rect x="3.3" y="4.2" width="5.4" height="3.6" rx="0.6" fill="#fff"/></svg>
        <svg viewBox="0 0 12 12" aria-label="Email"><circle cx="6" cy="6" r="6" fill="var(--plum)"/><rect x="3" y="3.8" width="6" height="4.4" fill="#fff"/><path d="M3 3.8l3 2.4 3-2.4" fill="none" stroke="var(--plum)" stroke-width="0.7"/></svg>
        <svg viewBox="0 0 12 12" aria-label="Website"><circle cx="6" cy="6" r="6" fill="var(--plum)"/><circle cx="6" cy="6" r="3" fill="none" stroke="#fff" stroke-width="0.8"/><path d="M3 6h6M6 3c-1.4 1.6-1.4 4.4 0 6M6 3c1.4 1.6 1.4 4.4 0 6" fill="none" stroke="#fff" stroke-width="0.6"/></svg>
      </div>
      <div class="details-row">
        <span>(000) 000-0000</span><span class="sep">|</span><span>(000) 000-0000</span><span class="sep">|</span><span>info@brightharbor.com</span><span class="sep">|</span><span>www.brightharbor.com</span>
      </div>
    </footer>
  </main>
</body>
</html>
```